Executive Performance Review mapped on J-curve

I need to turn an executive company performance review into a visual infographic. The list of accomplishments is grouped into four calendar quarters. Each quarter needs a subtle representation of the season. The four quarters and associated list of accomplishments need to be mapped to a J-curve. - Spreadsheet with accomplishments attached (Marlowbend)- Sample image of a J-curve. You can google J-curve to see more images.- The title should be "Danica Ostrander Year in Review"

Target Market(s)

Board of Directors

Requirements
Nice to have
• This will be presented to a company founder that is an artist and customer experience expert. He is very visual so a nice visual representation of the data will be impactful. He also uses the phrase that you have to live with or work with someone for four seasons before you really know them. This is why I have the seasons mapped to the quarters. The Fall season motif should be gloomy and stormy.

```html
<!DOCTYPE html>
<html lang="en">
<head>
<meta charset="utf-8">
<title>Danica Ostrander – Year One in Review</title>
<link rel="stylesheet" href="https://fonts.googleapis.com/css2?family=Source+Sans+3:wght@400;600;700&display=swap">
<style>
:root{
  --ink:#1e1e1e;
  --muted:#555;
  --summer-band:#f9c80e; --summer-bg:#fffbe6; --summer-pill:#fde68a;
  --fall-band:#4d5f66;   --fall-bg:#dde8e8;   --fall-pill:#9aabb0;
  --winter-band:#a9dbe8; --winter-bg:#eef8fb; --winter-pill:#cdeef5;
  --spring-band:#c6e04a; --spring-bg:#f3f8dc; --spring-pill:#dcefa0;
  --value-band:#2f8a3c;  --value-pill:#7fae84;
  --curve:#a8a8a8;
}
*{margin:0;padding:0;box-sizing:border-box}
html,body{width:1200px;height:653px;overflow:hidden;background:#fff}
body{position:relative;font-family:"Source Sans 3",Arial,sans-serif;color:var(--ink)}
.title-block{position:absolute;left:33px;top:24px;line-height:1.15}
.title-block h1{font-size:12.5px;font-weight:700;letter-spacing:.1px}
.title-block .date{font-size:11px}
.title-block .company{font-size:8.5px;color:var(--muted)}
.season{position:absolute;top:69px;height:547px}
.season .band{height:17px;color:#fff;font-weight:700;font-size:11.5px;text-align:center;line-height:17px;letter-spacing:.2px}
.season .pill{position:absolute;top:18px;left:50%;transform:translateX(-50%);width:100px;height:16px;border-radius:0 0 6px 6px;font-size:8.5px;font-weight:700;text-align:center;line-height:16px}
.summer{left:33px;width:227px;background:var(--summer-bg)}
.summer .band{background:var(--summer-band)} .summer .pill{background:var(--summer-pill)}
.fall{left:260px;width:228px;background:var(--fall-bg)}
.fall .band{background:var(--fall-band)} .fall .pill{background:var(--fall-pill)}
.winter{left:488px;width:230px;background:var(--winter-bg)}
.winter .band{background:var(--winter-band)} .winter .pill{background:var(--winter-pill)}
.spring{left:718px;width:230px;background:var(--spring-bg)}
.spring .band{background:var(--spring-band)} .spring .pill{background:var(--spring-pill)}
.value{left:948px;width:224px;background:linear-gradient(180deg,#cfe0d0 0%,#b7d3b9 60%,#8fbf8f 100%)}
.value .band{background:var(--value-band)} .value .pill{background:var(--value-pill);color:#fff}
.divider{position:absolute;top:86px;height:530px;border-left:1px dashed rgba(0,0,0,.18)}
.scene{position:absolute;left:0;top:0;width:1200px;height:653px}
.group{position:absolute;font-size:8.6px;line-height:13.6px}
.group h2{font-size:9px;font-weight:700;letter-spacing:.2px;line-height:12px}
.group ul{list-style:none}
.group li{padding-left:7px;text-indent:-7px}
.group li::before{content:"• "}
.group li.wrap{line-height:9px;margin-bottom:4px;margin-top:2px}
.icon{position:absolute;width:16px;height:16px}
.greenfield{position:absolute;left:974px;top:318px;font-size:10.5px;line-height:15.5px;color:#163d1c}
.greenfield h2{font-size:9.5px;font-weight:700;line-height:13px}
.greenfield ul{list-style:none}
.greenfield li::before{content:"• "}
.stage{position:absolute;top:600px;font-size:9px;font-weight:700;text-align:center;letter-spacing:.3px}
.stage.light{color:#fff}
.kpi{position:absolute;width:56px;height:56px;border-radius:50%;display:flex;flex-direction:column;align-items:center;justify-content:center;color:#fff;font-size:7.5px;font-weight:700;line-height:9px;text-align:center}
.kpi .coin{width:10px;height:10px;border:1.3px solid #fff;border-radius:3px 3px 5px 5px;margin-bottom:2px}
</style>
</head>
<body>

<header class="title-block">
  <h1>DANICA OSTRANDER - YEAR ONE IN REVIEW</h1>
  <div class="date">JULY 1, 2019</div>
  <div class="company">KEELROW STUDIO, INC.</div>
</header>

<section class="season summer"><div class="band">SUMMER - ASSESSMENT</div><div class="pill">Q3 2018</div></section>
<section class="season fall"><div class="band">FALL - STABLIZE</div><div class="pill">Q4 2018</div></section>
<section class="season winter"><div class="band">WINTER - STRATACTICAL</div><div class="pill">Q1 2019</div></section>
<section class="season spring"><div class="band">SPRING - STRATEGIC</div><div class="pill">Q2 2019</div></section>
<section class="season value"><div class="band">VALUE CREATION</div><div class="pill">2020+</div></section>

<div class="divider" style="left:260px"></div>
<div class="divider" style="left:488px"></div>
<div class="divider" style="left:718px"></div>
<div class="divider" style="left:948px"></div>

<svg class="scene" viewBox="0 0 1200 653" aria-hidden="false">
  <defs>
    <linearGradient id="seasonGround" x1="0" x2="1" y1="0" y2="0" gradientUnits="userSpaceOnUse" x1a="0">
      <stop offset="0" stop-color="#f6c410"/>
      <stop offset="0.19" stop-color="#f8cd2a"/>
      <stop offset="0.235" stop-color="#5d6b70"/>
      <stop offset="0.38" stop-color="#6e7d82"/>
      <stop offset="0.43" stop-color="#d6f0f8"/>
      <stop offset="0.6" stop-color="#e3f5fb"/>
      <stop offset="0.64" stop-color="#c8e36a"/>
      <stop offset="0.8" stop-color="#8cc84d"/>
      <stop offset="1" stop-color="#2b7a30"/>
    </linearGradient>
    <linearGradient id="groundX" x1="33" x2="1172" y1="0" y2="0" gradientUnits="userSpaceOnUse">
      <stop offset="0" stop-color="#f6c410"/>
      <stop offset="0.19" stop-color="#f8cd2a"/>
      <stop offset="0.215" stop-color="#5d6b70"/>
      <stop offset="0.38" stop-color="#6e7d82"/>
      <stop offset="0.43" stop-color="#d6f0f8"/>
      <stop offset="0.6" stop-color="#e3f5fb"/>
      <stop offset="0.625" stop-color="#c8e36a"/>
      <stop offset="0.8" stop-color="#86c34b"/>
      <stop offset="1" stop-color="#2b7a30"/>
    </linearGradient>
  </defs>
  <path role="img" aria-label="Seasonal ground scenes under the curve: sunny beach with palms, stormy autumn rain, snowy winter field, spring meadow with flowers and butterflies, deep green growth"
        fill="url(#groundX)"
        d="M33,472 C120,505 250,535 371,536 C470,537 540,520 602,496 C700,460 770,430 837,388 C930,330 1000,265 1064,206 L1172,88 L1172,616 L33,616 Z"/>
  <path fill="none" stroke="var(--curve)" stroke-width="4" stroke-linecap="round"
        d="M33,472 C120,505 250,535 371,536 C470,537 540,520 602,496 C700,460 770,430 837,388 C930,330 1000,265 1064,206 L1160,101"/>
  <polygon points="1172,86 1151,96 1164,108" fill="var(--curve)"/>
  <circle cx="136" cy="510" r="32" fill="#fde68a" opacity=".8"/>
  <circle cx="371" cy="536" r="32" fill="#7d8c92" opacity=".8"/>
  <circle cx="602" cy="499" r="32" fill="#d4eff6" opacity=".9"/>
  <circle cx="837" cy="388" r="32" fill="#e3f19c" opacity=".9"/>
  <circle cx="1062" cy="206" r="33" fill="#5aa364" opacity=".9"/>
</svg>

<div class="kpi" style="left:108px;top:482px;background:var(--summer-band)"><span class="coin"></span>$3.8M<br>1.44%</div>
<div class="kpi" style="left:343px;top:508px;background:var(--fall-band)"><span class="coin"></span>$4.4M<br>0.58%</div>
<div class="kpi" style="left:574px;top:471px;background:var(--winter-band)"><span class="coin"></span>$4.8M<br>12.84%</div>
<div class="kpi" style="left:809px;top:360px;background:var(--spring-band)"><span class="coin"></span>$4.7M<br>8.24%</div>
<div class="kpi" style="left:1034px;top:178px;background:var(--value-band)"><span class="coin"></span>$35M<br>15%</div>

<!-- Summer -->
<svg class="icon" style="left:38px;top:113px" viewBox="0 0 16 16"><path d="M9 2h5v5M14 2 7 9M12 10v4H2V4h4" fill="none" stroke="#333" stroke-width="1.3"/></svg>
<div class="group" style="left:64px;top:110px">
  <h2>TRANSITIONS</h2>
  <ul style="line-height:11.6px"><li>RO Transition from Ravi &amp; Imre</li><li>Start CR Office Initiative</li><li>Tactical Ops transition from Ravi</li><li>Formalize Exec Team</li></ul>
</div>
<svg class="icon" style="left:38px;top:184px" viewBox="0 0 16 16"><g fill="none" stroke="#333" stroke-width="1.1"><rect x="1" y="6" width="4" height="4"/><rect x="10" y="1" width="4" height="4"/><rect x="10" y="11" width="4" height="4"/><path d="M5 8h3M8 3v10M8 3h2M8 13h2"/></g></svg>
<div class="group" style="left:64px;top:181px">
  <h2>BIZ ARCHITECTURE</h2>
  <ul><li>Independent Financial Audit</li><li>Organizational Audit - Structure</li><li>Organizational Audit - People</li><li>XF Framework - ESU</li><li>Defined Utilization, Realization, Availability</li></ul>
</div>
<svg class="icon" style="left:37px;top:274px" viewBox="0 0 16 16"><g fill="none" stroke="#333" stroke-width="1.1"><circle cx="13" cy="4" r="2"/><path d="M1 1l3 3M4 1 1 4M1 15l3-3M4 15l-3-3M3 10c4-1 4-6 8-6"/></g></svg>
<div class="group" style="left:64px;top:272px">
  <h2>STRATEGY</h2>
  <ul><li>Effective Strategy Meeting</li><li class="wrap">Strategic Themes 2018 - 2020: Stablize,<br>Accelerate, Surge</li><li>Business Drivers: Drive Revenue, Improve</li><li>Keelrower Experience, Increase Brand Awareness</li></ul>
</div>
<svg class="icon" style="left:38px;top:362px" viewBox="0 0 16 16"><g fill="none" stroke="#333" stroke-width="1.1"><path d="M2 7l6-6h6v6l-6 6z"/><circle cx="11" cy="4" r="1"/></g></svg>
<div class="group" style="left:64px;top:359px">
  <h2>SALES</h2>
  <ul><li>Tallowmere Account Transition</li><li>QLV Account Transition</li><li class="wrap">2 year Managed Services Engagement<br>Model</li></ul>
</div>

<!-- Fall -->
<svg class="icon" style="left:266px;top:112px" viewBox="0 0 16 16"><g fill="none" stroke="#333" stroke-width="1.1"><rect x="1" y="6" width="4" height="4"/><rect x="10" y="1" width="4" height="4"/><rect x="10" y="11" width="4" height="4"/><path d="M5 8h3M8 3v10M8 3h2M8 13h2"/></g></svg>
<div class="group" style="left:291px;top:109px">
  <h2>BIZ ARCHITECTURE</h2>
  <ul><li class="wrap" style="margin-top:0">XF Framework - Functional Meetings &amp;<br>Scrum of Scrums</li><li>Structured Reorg</li><li>Implemented Reorg</li><li>Quarterly Org Iteration cadence</li><li>Defined Key Hire Plan</li><li>CR Office Operational</li><li>Time Accountability</li><li>Tools ReConfig</li><li>Org Structure v1</li></ul>
</div>
<svg class="icon" style="left:266px;top:266px" viewBox="0 0 16 16"><g fill="none" stroke="#333" stroke-width="1.1"><circle cx="13" cy="4" r="2"/><path d="M1 1l3 3M4 1 1 4M1 15l3-3M4 15l-3-3M3 10c4-1 4-6 8-6"/></g></svg>
<div class="group" style="left:291px;top:264px"><h2>STRATEGY</h2><ul><li>Internal QBR Accountability</li></ul></div>
<svg class="icon" style="left:266px;top:303px" viewBox="0 0 16 16"><g fill="none" stroke="#333" stroke-width="1.1"><path d="M2 7l6-6h6v6l-6 6z"/><circle cx="11" cy="4" r="1"/></g></svg>
<div class="group" style="left:291px;top:300px"><h2>SALES</h2><ul><li>Brightfen QBR</li><li>Tallowmere QBR</li></ul></div>

<!-- Winter -->
<svg class="icon" style="left:495px;top:112px" viewBox="0 0 16 16"><g fill="none" stroke="#333" stroke-width="1.1"><rect x="1" y="6" width="4" height="4"/><rect x="10" y="1" width="4" height="4"/><rect x="10" y="11" width="4" height="4"/><path d="M5 8h3M8 3v10M8 3h2M8 13h2"/></g></svg>
<div class="group" style="left:520px;top:110px">
  <h2>BIZ ARCHITECTURE</h2>
  <ul><li>XF Framework - Progress Demos</li><li>Org Structure - COE's</li><li>Stablize Accounting &amp; Finance</li><li>Exec Hiring Process</li></ul>
</div>
<svg class="icon" style="left:495px;top:188px" viewBox="0 0 16 16"><g fill="none" stroke="#333" stroke-width="1.2"><circle cx="6.5" cy="6.5" r="5"/><path d="M10 10l5 5"/></g></svg>
<div class="group" style="left:520px;top:188px"><h2>KEY HIRES</h2><ul><li>Controller</li><li>Director CX</li></ul></div>
<svg class="icon" style="left:495px;top:241px" viewBox="0 0 16 16"><g fill="none" stroke="#333" stroke-width="1.1"><circle cx="13" cy="4" r="2"/><path d="M1 1l3 3M4 1 1 4M1 15l3-3M4 15l-3-3M3 10c4-1 4-6 8-6"/></g></svg>
<div class="group" style="left:520px;top:239px"><h2>STRATEGY</h2><ul><li>Founders removed from front line activity</li><li>Keelrow QBR - Goal Setting &amp; Tracking</li></ul></div>
<svg class="icon" style="left:495px;top:292px" viewBox="0 0 16 16"><g fill="none" stroke="#333" stroke-width="1.1"><path d="M2 7l6-6h6v6l-6 6z"/><circle cx="11" cy="4" r="1"/></g></svg>
<div class="group" style="left:520px;top:289px"><h2>SALES</h2><ul><li>QLV QBR</li><li>Tallowmere QBR</li></ul></div>

<!-- Spring -->
<svg class="icon" style="left:725px;top:112px" viewBox="0 0 16 16"><g fill="none" stroke="#333" stroke-width="1.1"><rect x="1" y="6" width="4" height="4"/><rect x="10" y="1" width="4" height="4"/><rect x="10" y="11" width="4" height="4"/><path d="M5 8h3M8 3v10M8 3h2M8 13h2"/></g></svg>
<div class="group" style="left:749px;top:110px">
  <h2>BIZ ARCHITECTURE</h2>
  <ul><li class="wrap" style="margin-top:0">XF Framework - Ideation Process &amp;<br>Sales Cadence</li><li>Consulting Levels &amp; Salary Bands</li><li>Roles &amp; Responsibilities</li></ul>
</div>
<svg class="icon" style="left:725px;top:181px" viewBox="0 0 16 16"><g fill="none" stroke="#333" stroke-width="1.2"><circle cx="6.5" cy="6.5" r="5"/><path d="M10 10l5 5"/></g></svg>
<div class="group" style="left:749px;top:180px"><h2>KEY HIRES</h2><ul><li>Interim HR</li><li>Provisional Client Partner</li><li>Acting Director 1</li><li>Acting Director 2</li><li>Client Partner 1</li><li>Sales Exec 1</li></ul></div>
<svg class="icon" style="left:725px;top:289px" viewBox="0 0 16 16"><g fill="none" stroke="#333" stroke-width="1.1"><path d="M2 7l6-6h6v6l-6 6z"/><circle cx="11" cy="4" r="1"/></g></svg>
<div class="group" style="left:749px;top:285px"><h2>SALES</h2><ul><li>Tiered Pricing Managed Services</li><li>Opened Glasshaven Door</li><li class="wrap" style="margin-top:1px">Flipped focus from operationaly run<br>company to sales/marketing<br>driven org</li><li>Fernlow Direct</li></ul></div>

<!-- Value creation -->
<div class="greenfield">
  <h2>GREENFIELD</h2>
  <ul><li>Set 2020 Goals</li><li>Schedule QBRs 1 year out</li><li>Financial Projections</li><li>Fully Functional Leadership Team</li><li>Robust Sales Team</li></ul>
</div>

<div class="stage" style="left:33px;width:207px">STORMING</div>
<div class="stage light" style="left:260px;width:228px">ACTIVITY</div>
<div class="stage" style="left:488px;width:230px">MARLOWBEND</div>
<div class="stage" style="left:718px;width:230px">OUTCOMES</div>
<div class="stage light" style="left:948px;width:224px">SCALABILITY</div>

</body>
</html>
```